Business card design Needed for new logo / Construction business, home extensions and new builds

We need a business card design using our new logo files which i will attach to this project :)

We are a small construction business specialising in home extensions, new builds and property development. We are very ambitious and would appreciate professional and elegant designs for our new business card.

Very serious about using the services on MakerQuarry and recently acquired our new logo from here :)

Please get involved, i will feedback when i can as i am very busy but can respond daily, thanks

Target Market(s)

People that want to build onto their houses, new building developments or adding too their existing property

Industry/Entity Type

Construction

Contact Information for Business Card

Renwick Tolliver Construction, Lionel Ashby (Managing Director), Tel 07822254961, email - info@renwick-tolliver, www.renwick-tolliver.co.uk

Colors

Designer to choose colors to be used in the design.

Requirements
Must have
• I like a deep grey on the back please. A lot of you have provided black from and back, try mixing things up a little. The black looks cool 😎 Thanks

```html
<!DOCTYPE html>
<html lang="en">
<head>
<meta charset="utf-8">
<title>Renwick Tolliver Construction — Business Card</title>
<link rel="stylesheet" href="https://fonts.googleapis.com/css2?family=Open+Sans:wght@400;600;700&display=swap">
<style>
  :root {
    --page: #e9e9ec;
    --card: #1e1e23;
    --gold: #d9a42a;
    --gold-light: #f0c860;
    --silver: #c9cbd0;
    --text: #ffffff;
  }
  * { box-sizing: border-box; margin: 0; padding: 0; }
  html, body { width: 1200px; height: 780px; overflow: hidden; }
  body {
    background: var(--page);
    font-family: "Open Sans", Arial, sans-serif;
    display: flex;
    align-items: center;
    justify-content: center;
    gap: 40px;
  }
  .card {
    position: relative;
    width: 540px;
    height: 350px;
    background: var(--card);
    border-left: 2px solid var(--gold);
    border-bottom: 2px solid var(--gold);
    overflow: hidden;
  }
  /* front */
  .card-front { display: flex; align-items: center; justify-content: center; }
  .brand { display: flex; align-items: center; gap: 12px; }
  .brand-mark { width: 18px; height: 18px; background: var(--gold); flex: none; }
  .brand-name {
    color: var(--gold);
    font-weight: 600;
    letter-spacing: 0.06em;
    text-transform: uppercase;
    line-height: 1.3;
  }
  .card-front .brand-name { font-size: 22px; }
  /* back */
  .holder {
    position: absolute;
    top: 30px;
    right: 46px;
    text-align: right;
  }
  .holder-name { font-size: 27px; font-weight: 700; line-height: 1.1; }
  .holder-first { color: var(--silver); }
  .holder-last { color: var(--gold-light); }
  .holder-role { color: var(--text); font-size: 13px; font-weight: 600; margin-top: 4px; }
  .holder-bar {
    position: absolute;
    top: 28px;
    right: 0;
    width: 30px;
    height: 34px;
    background: linear-gradient(90deg, var(--gold), var(--gold-light));
  }
  .card-back .brand { position: absolute; left: 40px; top: 130px; }
  .card-back .brand-name { font-size: 17px; }
  .address {
    position: absolute;
    left: 40px;
    top: 196px;
    color: var(--text);
    font-size: 13px;
    line-height: 1.45;
  }
  .contacts {
    position: absolute;
    left: 40px;
    top: 252px;
    list-style: none;
    color: var(--text);
    font-size: 13px;
  }
  .contacts li { display: flex; align-items: center; gap: 9px; line-height: 22px; }
  .contacts svg { width: 13px; height: 13px; fill: none; stroke: var(--gold); stroke-width: 1.6; flex: none; }
</style>
</head>
<body>
  <section class="card card-front" aria-label="Card front">
    <div class="brand">
      <span class="brand-mark"></span>
      <span class="brand-name">Renwick Tolliver<br>Construction</span>
    </div>
  </section>

  <section class="card card-back" aria-label="Card back">
    <div class="holder">
      <p class="holder-name"><span class="holder-first">Lionel</span> <span class="holder-last">Ashby</span></p>
      <p class="holder-role">Managing Director</p>
    </div>
    <span class="holder-bar"></span>

    <div class="brand">
      <span class="brand-mark"></span>
      <span class="brand-name">Renwick Tolliver<br>Construction</span>
    </div>

    <p class="address">Harrow Lane, Westbury<br>Dorset, DT4 7QN</p>

    <ul class="contacts">
      <li>
        <svg viewBox="0 0 16 16"><path d="M3 2h3l1.5 3.5-2 1.3a8 8 0 0 0 3.7 3.7l1.3-2L14 10v3a1 1 0 0 1-1 1A11 11 0 0 1 2 3a1 1 0 0 1 1-1z"/></svg>
        0782 225 4961
      </li>
      <li>
        <svg viewBox="0 0 16 16"><rect x="1.5" y="3.5" width="13" height="9"/><path d="M1.5 3.5 8 9l6.5-5.5"/></svg>
        info@renwick-tolliver.co.uk
      </li>
      <li>
        <svg viewBox="0 0 16 16"><circle cx="8" cy="8" r="6.5"/><path d="M1.5 8h13M8 1.5c-3 3.5-3 9.5 0 13M8 1.5c3 3.5 3 9.5 0 13"/></svg>
        www.renwick-tolliver.co.uk
      </li>
    </ul>
  </section>
</body>
</html>
```